New Innovative Counselling and psychotherapy Service needs Business Card design

Keep it simple and professional. On one side, just company name and logo (perhaps in all blue) and maybe a tag line.

On other side (all white) my name and Qualifications in centre

Industry/Entity Type

Health And Wellness

Contact Information for Business Card

Dara Whelby
Counsellor & Psychotherapist
BSc (Psychol.), BA, Dip. (Couns. & Psych.), PG.Cert (CBT), FGTrK, ONRE

I will also require Mobile no, Email and web site address of which I'll pass on to final designer.

Font styles to use
Sans Serif

Requirements
Must have
• My Logo Only and please use the colours in logo that is in it.
Should not have
• Any other images

```html
<!DOCTYPE html>
<html lang="en">
<head>
<meta charset="utf-8">
<title>Brightlane – Business Card</title>
<link href="https://fonts.googleapis.com/css2?family=Work+Sans:wght@300;400;500;600&display=swap" rel="stylesheet">
<style>
  :root {
    --stage: #e6e7e9;
    --card-white: #ffffff;
    --card-dark: #2a2a2b;
    --band-dark: #2e2f31;
    --brand-blue: #3aa6dc;
    --brand-green: #7dbb42;
    --ink: #333538;
    --ink-soft: #55585c;
    --pale-blue: #dcedf8;
    --pale-green: #e9f3dc;
  }
  * { box-sizing: border-box; margin: 0; padding: 0; }
  html, body { width: 1200px; height: 963px; overflow: hidden; }
  body {
    background: var(--stage);
    font-family: "Work Sans", Arial, sans-serif;
    color: var(--ink);
    position: relative;
  }
  .card {
    position: absolute;
    left: 250px;
    width: 700px;
    height: 400px;
    border-radius: 18px;
    overflow: hidden;
    box-shadow: 0 10px 30px rgba(0,0,0,.15);
  }
  /* Front */
  .card-front { top: 50px; background: var(--card-white); }
  .name-band {
    position: absolute;
    left: 0; top: 34px;
    width: 420px; height: 62px;
    background: var(--band-dark);
    padding: 6px 0 0 40px;
  }
  .person-name {
    font-size: 30px;
    font-weight: 500;
    letter-spacing: .5px;
    text-transform: uppercase;
    color: var(--brand-blue);
    line-height: 1.05;
  }
  .person-role {
    font-size: 15px;
    font-weight: 400;
    color: var(--brand-green);
    margin-top: 2px;
  }
  .qualifications {
    position: absolute;
    left: 40px; top: 112px;
    width: 260px;
    font-size: 15px;
    line-height: 1.3;
    color: var(--ink);
  }
  .contact-list {
    position: absolute;
    left: 40px; top: 250px;
    list-style: none;
    font-size: 15px;
    line-height: 1.55;
    color: var(--ink);
  }
  .contact-list li { display: flex; align-items: center; gap: 10px; }
  .contact-list svg { width: 12px; height: 12px; flex: none; }
  .web-accent { color: var(--brand-blue); }
  .brand-lockup {
    position: absolute;
    left: 440px; top: 38px;
    display: flex; align-items: center; gap: 12px;
  }
  .brand-dot {
    width: 44px; height: 44px; border-radius: 50%;
    background: var(--brand-blue);
  }
  .brand-name {
    font-size: 34px;
    font-weight: 300;
    color: var(--ink);
    letter-spacing: .5px;
  }
  .brand-watermark {
    position: absolute;
    left: 420px; top: 170px;
    width: 320px; height: 260px;
    border-radius: 50%;
    background: radial-gradient(circle at 40% 45%, var(--pale-green) 0%, var(--pale-blue) 55%, rgba(220,237,248,0) 72%);
  }
  /* Back */
  .card-back { top: 513px; background: var(--card-dark); }
  .back-texture {
    position: absolute; inset: 0;
    background: var(--card-dark);
  }
  .back-lockup {
    position: absolute;
    left: 50%; top: 50%;
    transform: translate(-50%, -50%);
    display: flex; align-items: center; gap: 14px;
  }
  .back-lockup .brand-name { color: var(--brand-blue); }
</style>
</head>
<body>

  <section class="card card-front" aria-label="Business card front">
    <div class="brand-watermark" role="img" aria-label="Large faint brand symbol decoration"></div>

    <header class="name-band">
      <h1 class="person-name">Dara Whelby</h1>
      <p class="person-role">Counsellor &amp; Psychotherapist</p>
    </header>

    <p class="qualifications">BSc (Psychol.), BA, Dip. (Couns. &amp; Psych.), PG.Cert (CBT), FGTrK, ONRE</p>

    <ul class="contact-list">
      <li>
        <svg viewBox="0 0 12 12" aria-hidden="true"><path d="M3 1l2 2.5-1.2 1.3c.6 1.4 1.5 2.3 2.9 2.9L8 6.5 10.5 8.5 9.3 10.8C5 10.5 1.5 7 1.2 2.7z" fill="var(--brand-blue)"/></svg>
        555-014-2876
      </li>
      <li>
        <svg viewBox="0 0 12 12" aria-hidden="true"><rect x="1" y="2.5" width="10" height="7" fill="none" stroke="var(--brand-blue)" stroke-width="1.2"/><path d="M1 2.5l5 4 5-4" fill="none" stroke="var(--brand-blue)" stroke-width="1.2"/></svg>
        hello@brightlanecare.com
      </li>
      <li>
        <svg viewBox="0 0 12 12" aria-hidden="true"><circle cx="6" cy="6" r="5" fill="none" stroke="var(--brand-blue)" stroke-width="1.1"/><path d="M1 6h10M6 1c-2 2.5-2 7.5 0 10M6 1c2 2.5 2 7.5 0 10" fill="none" stroke="var(--brand-blue)" stroke-width=".9"/></svg>
        <span>www.<span class="web-accent">brightlanecare</span>.com</span>
      </li>
    </ul>

    <div class="brand-lockup">
      <span class="brand-dot" aria-hidden="true"></span>
      <span class="brand-name">Brightlane</span>
    </div>
  </section>

  <section class="card card-back" aria-label="Business card back">
    <div class="back-texture" role="img" aria-label="Subtle repeating brand pattern on dark background"></div>
    <div class="back-lockup">
      <span class="brand-dot" aria-hidden="true"></span>
      <span class="brand-name">Brightlane</span>
    </div>
  </section>

</body>
</html>
```